Valdor Corporate brochure

Valdor Investigative Group would like to focus this brochure to public corporations and private businesses in Alberta. the services offered in this brochure would include investigations for suspicious QVN claims, LTD health benefits claims, internal fraud and theft, theft of time or resources by offsite staff and pre-employment screening. our website has many of the information you will need. www.valdorvx.ca

```html
<!DOCTYPE html>
<html lang="en">
<head>
<meta charset="utf-8">
<title>Valdor Investigative Group – Services Brochure</title>
<link rel="stylesheet" href="https://fonts.googleapis.com/css2?family=Lato:wght@300;400&display=swap">
<style>
  :root {
    --page: #ffffff;
    --navy: #1b1a8a;
    --glow: #7ccdf4;
    --panel: rgba(160, 164, 220, 0.62);
    --text-light: #f4f5ff;
    --text-dark: #2a2c6a;
    --bullet: #2a2fb0;
    --tab: rgba(225, 232, 255, 0.55);
    --photo-blue: #27b8e0;
    --photo-brown: #5a3b22;
    --photo-orange: #a0683a;
  }
  * { box-sizing: border-box; margin: 0; padding: 0; }
  html, body { width: 1200px; height: 1000px; overflow: hidden; background: var(--page); }
  body { position: relative; font-family: "Lato", sans-serif; }

  .brochure {
    position: absolute; left: 42px; top: 263px; width: 1130px; height: 457px;
    background:
      radial-gradient(ellipse 330px 150px at 700px 0px, var(--glow) 0%, rgba(124,205,244,0.55) 35%, rgba(60,110,210,0.25) 70%, transparent 100%),
      radial-gradient(ellipse 700px 380px at 620px 120px, #3a5fcf 0%, var(--navy) 75%),
      var(--navy);
    box-shadow: 3px 4px 8px rgba(0,0,0,0.45);
    overflow: hidden;
  }

  .panel { position: absolute; background: var(--panel); }
  .panel-corporate { left: 3px; top: 15px; width: 223px; height: 262px; }
  .panel-domestic { left: 237px; top: 15px; width: 436px; height: 372px; }
  .panel-claims { left: 700px; top: 15px; width: 416px; height: 183px; }
  .panel-insurance { left: 700px; top: 207px; width: 416px; height: 237px; }

  .tab { position: absolute; height: 16px; background: var(--tab); }

  .heading {
    position: absolute; color: var(--text-light); font-weight: 300;
    text-transform: uppercase; font-size: 23.8px; line-height: 1; letter-spacing: 0.2px; white-space: nowrap;
  }
  .heading .sub { text-transform: none; color: var(--text-dark); font-size: 17.5px; }
  .heading-stack { font-size: 17px; line-height: 20px; letter-spacing: 0.3px; }

  .intro {
    position: absolute; font-size: 7.5px; color: var(--text-light); text-transform: uppercase;
    font-weight: 300; letter-spacing: 0.2px; white-space: nowrap; padding-bottom: 3px;
    border-bottom: 1px solid rgba(255,255,255,0.35);
  }

  .service-list { position: absolute; list-style: none; }
  .service-list li {
    position: relative; padding-left: 9px; font-size: 7.7px; font-weight: 300; color: var(--text-light);
    white-space: nowrap; height: 13.7px; line-height: 9px;
  }
  .service-list li::before {
    content: ""; position: absolute; left: 0; top: 2px; width: 5px; height: 5px;
    border-radius: 50%; background: var(--bullet);
  }
  .list-insurance li { height: 14.4px; }

  .claim-signs { position: absolute; left: 713px; top: 68px; width: 400px; list-style: none; }
  .claim-signs li {
    position: relative; padding-left: 9px; font-size: 7.3px; font-weight: 300; line-height: 8.6px;
    color: var(--text-light); margin-bottom: 6px;
  }
  .claim-signs li::before {
    content: ""; position: absolute; left: 0; top: 2px; width: 5px; height: 5px;
    border-radius: 50%; background: var(--bullet);
  }

  .photo { position: absolute; }
  .photo-world { left: 11px; top: 286px; width: 215px; height: 144px;
    background: radial-gradient(ellipse at 40% 30%, #9ff0ff 0%, var(--photo-blue) 40%, #0b3d8a 100%); }
  .photo-scales { left: 498px; top: 286px; width: 161px; height: 145px;
    background: radial-gradient(ellipse at 50% 50%, var(--photo-orange) 0%, var(--photo-brown) 45%, #1a120c 100%); }
  .photo-rescue { left: 1003px; top: 327px; width: 98px; height: 78px;
    background: linear-gradient(135deg, #5a6a48 0%, #c9a040 45%, #d0552a 70%, #3a3a34 100%); }

  .web { position: absolute; color: var(--text-light); font-size: 17px; font-weight: 300; letter-spacing: 0.4px; }
  .web-left { left: 251px; top: 416px; }
  .web-right { left: 967px; top: 421px; }
</style>
</head>
<body>
<main class="brochure">
  <section class="panel panel-corporate"></section>
  <section class="panel panel-domestic"></section>
  <section class="panel panel-claims"></section>
  <section class="panel panel-insurance"></section>

  <div class="tab" style="left:593px;top:30px;width:80px;"></div>
  <div class="tab" style="left:1063px;top:30px;width:53px;"></div>
  <div class="tab" style="left:593px;top:179px;width:80px;"></div>
  <div class="tab" style="left:1063px;top:216px;width:53px;"></div>

  <h2 class="heading" style="left:14px;top:26px;">Corporate <span class="sub">services</span></h2>
  <p class="intro" style="left:26px;top:58px;">Our corporate services are not limited to:</p>
  <ul class="service-list" style="left:16px;top:72px;">
    <li>Anton Piller Orders</li>
    <li>Competitive Intelligence</li>
    <li>Confidentiality and Non-compete Agreements</li>
    <li>Conflict of Interest Investigations</li>
    <li>Corporate Fraud / Theft</li>
    <li>Corporate &amp; Investor Due Diligence</li>
    <li>Electronic &amp; Intrusion Device Sweeping and Debugging</li>
    <li>Employee Integrity and Work Related Contracts</li>
    <li>Intellectual Property Rights Security</li>
    <li>Intrusion Testing</li>
    <li>Loss Prevention and Internal &amp; External Theft</li>
    <li>Patent, Trademark, &amp; Copyright Violations</li>
    <li>Pre-Employment Screening &amp; Internal Investigations</li>
    <li>Tenant Screening</li>
    <li>Workers Compensation and Disability Claim Investigations</li>
  </ul>

  <h2 class="heading" style="left:252px;top:26px;">Domestic Relations <span class="sub">services</span></h2>
  <p class="intro" style="left:253px;top:58px;width:300px;">Our domestic investigation services are not limited to:</p>
  <ul class="service-list" style="left:244px;top:75px;">
    <li>Conducting surveillance to determine Infidelity</li>
    <li>Determining income sources in regards to Maintenance Enforcement Orders</li>
    <li>Proving Child Custody Order requirements or breaches</li>
    <li>Monitoring Child Custody Transfers and Parental Access using discreet video photography</li>
    <li>Conducting Background Investigations, including Asset Determination and Criminal/Civil Court history</li>
    <li>Locate of family members, friends and persons of interest</li>
  </ul>

  <h2 class="heading" style="left:253px;top:175px;">Litigation Support <span class="sub">services</span></h2>
  <p class="intro" style="left:253px;top:208px;width:300px;">Our litigation support services are not limited to:</p>
  <ul class="service-list" style="left:244px;top:226px;">
    <li>Comprehensive Background Investigations</li>
    <li>Insurance Claim Investigations</li>
    <li>Surveillance</li>
    <li>Locating witnesses and involved parties</li>
    <li>Obtaining detailed Statements</li>
    <li>Statement Analysis</li>
    <li>Scene Investigations</li>
    <li>Process serving</li>
    <li>Business and Contract Disputes</li>
    <li>Subrogation efforts</li>
    <li>Coordinating of various experts as required on your behalf</li>
  </ul>

  <h2 class="heading heading-stack" style="left:716px;top:22px;">Workers' Compensation / Disability<br>Insurance Claims</h2>
  <ul class="claim-signs">
    <li>Inconsistent story by the claimant – the claimant does not have a firm grasp of the details surrounding the injury or the claimant frequently alters the information pertaining to the incident.</li>
    <li>A disgruntled or underperforming employee is more likely to put forth a fraudulent claim.</li>
    <li>Financial difficulties. A claimant will utilize the paid benefits of the claim and seek additional employment to relieve their financial hardship – ie. "double dipping". When you attempt to contact the claimant at home while they are off work, they rarely answer the telephone or return your call using a cell phone rather than their home phone.</li>
    <li>The claimant consistently misses physiotherapy sessions or doctor's appointments. A legitimately injured worker will want to get back to work and make the therapy a priority in their life.</li>
    <li>The claimant is performing activities in their personal life that are in direct contrast to their injuries. You often hear about these activities through other employees.</li>
  </ul>

  <h2 class="heading" style="left:711px;top:213px;">Insurance</h2>
  <p class="intro" style="left:717px;top:241px;width:300px;">Our insurance related services can include but are not limited to:</p>
  <ul class="service-list list-insurance" style="left:708px;top:256px;">
    <li>SIU claim investigations</li>
    <li>Video Surveillance (Bodily Injury)</li>
    <li>Positive claimant identification</li>
    <li>Discreet video surveillance to provide an objective documentation of claimant's current physical condition</li>
    <li>Verification of current employment status</li>
    <li>Identification of all bodily injury history and claims pre-and-post date of loss</li>
    <li>Financial assessment</li>
    <li>Identification and location of insureds, witnesses or persons of interest</li>
    <li>Professional interviews and securing of admissible statements</li>
    <li>Scene examination and securing of physical and photographic evidence</li>
    <li>Verification of underwriting and bond application information</li>
    <li>Liaison with law enforcement and government regulators</li>
    <li>Full subrogation and litigation support</li>
  </ul>

  <div class="photo photo-world" role="img" aria-label="Silhouettes of business people shaking hands in front of a glowing world map"></div>
  <div class="photo photo-scales" role="img" aria-label="Brass scales of justice and a gavel in a law library"></div>
  <div class="photo photo-rescue" role="img" aria-label="Emergency workers in high-visibility vests tending an injured worker"></div>

  <p class="web web-left">www.valdorvx.ca</p>
  <p class="web web-right">www.valdorvx.ca</p>
</main>
</body>
</html>
```